A new presentation to our clients

we are a Real Estate agency, our website is www.lumibrasa.com and it’s time to have a new, fashion and remarcable Business Card. we want to differentiate ourselves from other companies so we want a business card that differentiates us. we want the business card to impact our customers. in the competitive market that we have today, we have to be different and it is this difference that we seek

Target Market(s)

Real Estate Clients

Contact Information for Business Card

We search a totaly diferent card from the usual

Font styles to use
Sans Serif

Colors
e34197

Requirements
Must have
• Logo, adress, phone contact, e-mail, photo, and our website
Nice to have
• We would like to see a modern business card
Should not have
• Houses or building draws

```html
<!DOCTYPE html>
<html lang="en">
<head>
<meta charset="UTF-8">
<title>Lumi Brasa – Business Card</title>
<link href="https://fonts.googleapis.com/css2?family=Open+Sans:wght@400;600&family=Roboto:wght@300;400;500;700&display=swap" rel="stylesheet">
<style>
  :root {
    --pink: #e3226f;
    --ink: #3f3f3f;
    --rule: #c4c4c4;
    --card-front: #eeeeee;
    --card-back: #1f1f1f;
    --stage: #8a8a8a;
  }
  * { margin: 0; padding: 0; box-sizing: border-box; }
  html, body { width: 1200px; height: 1200px; overflow: hidden; }
  body { background: var(--stage); position: relative; font-family: "Open Sans", sans-serif; }

  .card { position: absolute; top: 310px; width: 365px; height: 594px; }
  .card--front { left: 234px; background: var(--card-front); text-align: center; }
  .card--back { left: 627px; width: 370px; background: var(--card-back); }

  .brand-name {
    position: absolute; top: 440px; left: 0; right: 0; top: 140px;
    font-family: "Roboto", sans-serif; font-weight: 500; font-size: 50px;
    color: var(--pink); letter-spacing: 0.5px;
  }
  .person { position: absolute; top: 320px; left: 0; right: 0; }
  .person__name { font-family: "Roboto", sans-serif; font-weight: 700; font-size: 21px; color: var(--pink); line-height: 24px; }
  .person__role { font-size: 16px; color: var(--ink); line-height: 22px; }

  .icon-row { position: absolute; top: 375px; left: 72px; width: 220px; height: 22px; display: flex; align-items: center; gap: 6px; }
  .icon-row__rule { flex: 1; height: 1px; background: var(--rule); }
  .icon { width: 22px; height: 20px; background: var(--pink); display: flex; align-items: center; justify-content: center; }
  .icon svg { width: 14px; height: 14px; }

  .contacts { position: absolute; top: 400px; left: 0; right: 0; font-size: 17px; line-height: 21.5px; color: var(--ink); }
  .divider { position: absolute; top: 496px; left: 72px; width: 220px; height: 1px; background: var(--rule); }
  .address { position: absolute; top: 505px; left: 0; right: 0; font-size: 17px; line-height: 21px; color: var(--ink); }

  .slogan { position: absolute; left: 43px; top: 100px; font-family: "Roboto", sans-serif; color: var(--pink); line-height: 1; }
  .slogan span { display: block; }
  .slogan__the { font-weight: 400; font-size: 118px; letter-spacing: 26px; }
  .slogan__house { font-weight: 700; font-size: 80px; margin-top: 24px; letter-spacing: -1px; }
  .slogan__of { font-weight: 400; font-size: 66px; margin-top: 22px; }
  .slogan__dreams { font-weight: 700; font-size: 66px; margin-top: 16px; letter-spacing: -1px; }
</style>
</head>
<body>
  <section class="card card--front">
    <div class="brand-name">Lumi Brasa</div>

    <div class="person">
      <div class="person__name">DANIEL MOREIRA</div>
      <div class="person__role">Managing Director</div>
    </div>

    <div class="icon-row">
      <span class="icon-row__rule"></span>
      <span class="icon" aria-label="Phone">
        <svg viewBox="0 0 14 14"><path d="M1 5 Q7 0 13 5 L11 7 L9 5.5 L5 5.5 L3 7 Z M3 8 H11 L12 12 H2 Z" fill="#fff"/></svg>
      </span>
      <span class="icon" aria-label="Fax">
        <svg viewBox="0 0 14 14"><rect x="4" y="1" width="6" height="4" fill="#fff"/><rect x="1" y="5" width="12" height="5" fill="#fff"/><rect x="4" y="9" width="6" height="4" fill="#fff" stroke="#e3226f" stroke-width="0.8"/></svg>
      </span>
      <span class="icon" aria-label="Email">
        <svg viewBox="0 0 14 14"><rect x="1" y="3" width="12" height="8" fill="#fff"/><path d="M1 3 L7 8 L13 3" fill="none" stroke="#e3226f" stroke-width="1"/></svg>
      </span>
      <span class="icon" aria-label="Website">
        <svg viewBox="0 0 14 14"><circle cx="7" cy="7" r="5.5" fill="#fff"/><path d="M1.5 7 H12.5 M7 1.5 Q4 7 7 12.5 M7 1.5 Q10 7 7 12.5" fill="none" stroke="#e3226f" stroke-width="0.9"/></svg>
      </span>
      <span class="icon-row__rule"></span>
    </div>

    <div class="contacts">
      <div>(+351) 210 458 302</div>
      <div>(+351) 210 458 309</div>
      <div>geral@lumibrasa.com</div>
      <div>www.lumibrasa.com</div>
    </div>

    <div class="divider"></div>

    <div class="address">
      <div>Av. Sol Poente, 214</div>
      <div>4410-086, Vale Claro</div>
    </div>
  </section>

  <section class="card card--back">
    <h1 class="slogan">
      <span class="slogan__the">THE</span>
      <span class="slogan__house">HOUSE</span>
      <span class="slogan__of">OF YOUR</span>
      <span class="slogan__dreams">DREAMS!</span>
    </h1>
  </section>
</body>
</html>
```